A Gallery type Web design

We are developing a Wordpress based website for a client that does design construction projects. E.g. Pools, Lobbies, Toilets, etc. The website will mainly be to showcase their past projects and the collections they have.
No programming required, we just need the designs!
A sample of what the client is looking for:
http://velmorati.it/
Pages to include:
• Home – A nice slider design to showcase selected photos
• Main Category Template
• Sub Category Template
• About us
• Contact us
Example of their Main Categories and their Sub Categories:
Collections - Granite
- Marble
- Sculpture
Projects - Private
- Public
- Commercial
- Overseas
Installation - Vanity tops
- Hall areas
- Toilets
The Main Category is to show a sample and link the user to the respective Sub Categories. The Sub Categories are to showcase all the photos they have from the category. Please leave a little space to add some text or caption for the photo.
Designs need to be mobile responsive!
I've attached their logo and some sample photos to use for mock ups. Let me know if you have any questions!

```html
<!DOCTYPE html>
<html lang="en">
<head>
<meta charset="utf-8">
<title>Petrana – Home</title>
<link rel="stylesheet" href="https://fonts.googleapis.com/css2?family=Arimo:wght@400;700&display=swap">
<style>
:root{
  --red:#e0201f;
  --ink:#1d1d1d;
  --body:#555555;
  --header-bg:#c9c9cb;
  --section-bg:#f3eeee;
  --footer-bg:#4a4a4a;
  --white:#ffffff;
}
*{margin:0;padding:0;box-sizing:border-box}
html,body{width:1013px;height:1200px;overflow:hidden}
body{font-family:"Arimo",Arial,sans-serif;background:var(--white);color:var(--ink);position:relative}

.site-header{position:absolute;left:0;top:0;width:1013px;height:117px;
  background:linear-gradient(180deg,#bfbfc2 0%,#d3d3d5 60%,#cbcbce 100%);
  border-bottom:3px solid var(--red)}
.brand{position:absolute;left:86px;top:22px;display:flex;align-items:center;gap:10px}
.brand-mark{width:22px;height:22px;background:var(--red)}
.brand-name{font-size:30px;font-weight:700;color:var(--red);letter-spacing:1px}
.call{position:absolute;right:85px;top:28px;font-size:21px;color:var(--ink)}
.call span{color:var(--red);margin-left:6px}
.main-nav{position:absolute;left:342px;top:82px;display:flex;height:32px}
.main-nav a{display:block;padding:0 19px;line-height:32px;font-size:13px;color:var(--white);text-decoration:none}
.main-nav a.active{background:var(--red)}

.hero{position:absolute;left:0;top:117px;width:1013px;height:476px;
  background:linear-gradient(100deg,#2a2a26 0%,#6a665a 35%,#a8a292 55%,#8a8474 75%,#4a4638 100%)}

.welcome{position:absolute;left:84px;top:636px;width:520px}
.welcome h1{font-size:27px;font-weight:400;color:var(--red);letter-spacing:.3px}
.welcome h2{font-size:16px;font-weight:400;color:var(--ink);margin-top:10px}
.welcome p{font-size:11.5px;line-height:18.6px;color:var(--body);margin-top:5px;width:510px}
.btn{position:absolute;left:404px;top:142px;width:98px;height:30px;background:var(--red);
  color:var(--white);font-size:12.5px;line-height:30px;text-align:center;border-radius:3px;text-decoration:none}
.welcome-photo{position:absolute;left:647px;top:638px;width:282px;height:159px;
  background:linear-gradient(120deg,#8a6a4a 0%,#4a4548 45%,#c8b9a0 75%,#6a5a48 100%)}

.projects{position:absolute;left:0;top:855px;width:1013px;height:261px;background:var(--section-bg);
  box-shadow:inset 0 6px 8px -6px rgba(0,0,0,.12)}
.projects h3{position:absolute;left:85px;top:26px;font-size:22px;font-weight:400;color:var(--red)}
.card{position:absolute;top:76px;width:262px;height:135px;
  background:linear-gradient(100deg,#2e2e2a 0%,#7a7466 45%,#b0aa98 70%,#6e685a 100%)}
.card-caption{position:absolute;left:0;bottom:0;width:100%;height:42px;background:rgba(30,30,30,.78);
  display:flex;align-items:center;justify-content:space-between;padding:0 12px 0 13px}
.card-caption span{color:var(--white);font-size:19px;letter-spacing:.5px}

.site-footer{position:absolute;left:0;top:1116px;width:1013px;height:84px;background:var(--footer-bg)}
.footer-nav{position:absolute;left:86px;top:24px;font-size:11.5px;color:var(--white)}
.footer-nav a{color:var(--white);text-decoration:none}
.footer-nav .sep{margin:0 14px}
.copyright{position:absolute;left:85px;top:53px;font-size:11.5px;color:var(--white)}
.social{position:absolute;left:681px;top:34px;display:flex}
.social a{display:block;width:42px;text-align:center;font-size:12px;line-height:16px;color:var(--white);text-decoration:none}
</style>
</head>
<body>
<header class="site-header">
  <div class="brand"><div class="brand-mark"></div><div class="brand-name">PETRANA</div></div>
  <div class="call">Call Now<span>(555) 318 4402</span></div>
  <nav class="main-nav">
    <a class="active" href="#">Home</a>
    <a href="#">Main Category Template</a>
    <a href="#">Sub Category Template</a>
    <a href="#">About us</a>
    <a href="#">Contact us</a>
  </nav>
</header>

<div class="hero" role="img" aria-label="Slider photo of an elegant interior with dining area, console table, lamps and mosaic floor"></div>

<section class="welcome">
  <h1>WELCOME TO PETRANA</h1>
  <h2>Sed ut perspiciatis unde omnis iste natus error sit voluptatem.</h2>
  <p>Lorem ipsum dolor sit amet, consectetur adipiscing elit, sed do eiusmod tempor incididunt ut labore et dolore magna aliqua. Ut enim ad minim veniam, quis nostrud exercitation ullamco laboris nisi ut cillum dolore eu fugiat nulla pariatur. Excepteur sint occaecat cupidatat non proident, sunt in culpa qui officia deserunt mollit anim id est laborum.</p>
  <a class="btn" href="#">Read More</a>
</section>
<div class="welcome-photo" role="img" aria-label="Photo of a mosaic-tiled fireplace wall with stacked firewood and a woven bowl"></div>

<section class="projects">
  <h3>PRIVATE PROJECT</h3>
  <div class="card" style="left:84px" role="img" aria-label="Public project interior photo">
    <div class="card-caption"><span>PUBLIC</span>
      <svg width="24" height="24" viewBox="0 0 24 24"><circle cx="12" cy="12" r="12" fill="#fff"/><path d="M6 12h11M12.5 7l5 5-5 5" stroke="#222" stroke-width="2.4" fill="none" stroke-linecap="round" stroke-linejoin="round"/></svg></div>
  </div>
  <div class="card" style="left:371px" role="img" aria-label="Commercial project interior photo">
    <div class="card-caption"><span>COMMERCIAL</span>
      <svg width="24" height="24" viewBox="0 0 24 24"><circle cx="12" cy="12" r="12" fill="#fff"/><path d="M6 12h11M12.5 7l5 5-5 5" stroke="#222" stroke-width="2.4" fill="none" stroke-linecap="round" stroke-linejoin="round"/></svg></div>
  </div>
  <div class="card" style="left:667px" role="img" aria-label="Overseas project interior photo">
    <div class="card-caption"><span>OVERSEAS</span>
      <svg width="24" height="24" viewBox="0 0 24 24"><circle cx="12" cy="12" r="12" fill="#fff"/><path d="M6 12h11M12.5 7l5 5-5 5" stroke="#222" stroke-width="2.4" fill="none" stroke-linecap="round" stroke-linejoin="round"/></svg></div>
  </div>
</section>

<footer class="site-footer">
  <nav class="footer-nav">
    <a href="#">Home</a><span class="sep">|</span><a href="#">Main Category Template</a><span class="sep">|</span><a href="#">Sub Category Template</a><span class="sep">|</span><a href="#">About us</a><span class="sep">|</span><a href="#">Contact us</a>
  </nav>
  <div class="copyright">Copyright © 2014 All Rights Reserved | Privacy Policy</div>
  <nav class="social" aria-label="Social links">
    <a href="#">Trill</a><a href="#">Fenno</a><a href="#">Gyre</a><a href="#">Lanx</a><a href="#">Pica</a><a href="#">Dobo</a>
  </nav>
</footer>
</body>
</html>
```